Custom unique Stationary design for Logistics company

We need a custom, unique , elegant and luxurious full stationary design using our new logo, following these guidelines:
1- Business card: double sided, both sides uses the navy blue as the background main color (same as the code of the navy blue used in our logo).
2- envelope and folder: also use the same navy blue as the main background color.
3- book cover( notepad cover) : same thing with the navy blue
4- letterhead: feel free to use the combination of the colors in our logo.
5- rest of the items are up to your creativity

Target Market(s)

corporates and other businesses

Industry/Entity Type

Logistics and heavy machines contractors

Requirements
Must have
• Letterhead, business card, envelope, notepad cover, paper, file
Nice to have
• navy blue to be main background color for business card, envelope, notepad cover

```html
<!DOCTYPE html>
<html lang="en">
<head>
<meta charset="utf-8">
<title>Harlow Freight – Business Card</title>
<link rel="stylesheet" href="https://fonts.googleapis.com/css2?family=Montserrat:wght@600;700&family=Roboto:wght@400;500&display=swap">
<style>
  :root {
    --navy: #0f4a73;
    --navy-deep: #0a2f52;
    --teal: #2d87ad;
    --orange: #f0562a;
    --ink: #1e5f86;
    --paper: #ffffff;
    --grey-text: #333a40;
    --backdrop: #e9e6e1;
  }
  * { margin: 0; padding: 0; box-sizing: border-box; }
  html, body { width: 1200px; height: 913px; overflow: hidden; }
  body { background: var(--backdrop); position: relative; font-family: "Roboto", Arial, sans-serif; }

  .card {
    position: absolute;
    width: 525px;
    height: 300px;
    border-radius: 4px;
    box-shadow: 0 14px 30px rgba(0,0,0,.22);
    overflow: hidden;
  }

  /* Front side */
  .card-front { left: 70px; top: 110px; background: var(--paper); }
  .front-brand {
    position: absolute; right: 40px; top: 42px;
    font-family: "Montserrat", Arial, sans-serif; font-weight: 700;
    font-size: 30px; letter-spacing: 1px; color: var(--ink);
    display: flex; align-items: center; gap: 10px;
  }
  .brand-dot { width: 14px; height: 14px; border-radius: 50%; background: var(--orange); }

  .holder { position: absolute; left: 40px; top: 112px; }
  .holder-name {
    font-family: "Montserrat", Arial, sans-serif; font-weight: 700;
    font-size: 19px; color: var(--ink); letter-spacing: .3px;
  }
  .holder-title {
    font-family: "Montserrat", Arial, sans-serif; font-weight: 600;
    font-size: 15px; color: var(--orange); margin-top: 2px;
  }
  .contact-list { list-style: none; margin-top: 14px; }
  .contact-list li {
    display: flex; align-items: center; gap: 9px;
    font-size: 13.5px; color: var(--grey-text); line-height: 20px;
  }
  .contact-list svg { width: 13px; height: 13px; flex: none; }

  .address-band {
    position: absolute; left: 0; bottom: 0; width: 100%; height: 46px;
    background: var(--navy);
    display: flex; align-items: center; padding-left: 40px; gap: 10px;
    color: #fff; font-size: 13.5px; letter-spacing: .2px;
  }
  .address-band svg.pin { width: 12px; height: 16px; }
  .band-chevrons { position: absolute; right: 26px; top: -16px; width: 70px; height: 40px; }

  /* Back side */
  .card-back {
    left: 605px; top: 500px;
    background: linear-gradient(160deg, var(--teal) 0%, var(--navy) 45%, var(--navy-deep) 100%);
    display: flex; align-items: center; justify-content: center;
  }
  .back-brand {
    font-family: "Montserrat", Arial, sans-serif; font-weight: 700;
    font-size: 44px; letter-spacing: 2px; color: #fff;
    display: flex; align-items: center; gap: 14px;
  }
  .back-brand .brand-dot { width: 20px; height: 20px; }
</style>
</head>
<body>

<section class="card card-front" aria-label="Business card front">
  <div class="front-brand"><span class="brand-dot"></span>HARLOW FREIGHT</div>

  <div class="holder">
    <h1 class="holder-name">DANE WHITLOCK</h1>
    <p class="holder-title">Managing Director</p>
    <ul class="contact-list">
      <li>
        <svg viewBox="0 0 12 12" aria-hidden="true"><rect x="3" y="0.5" width="6" height="11" rx="1.2" fill="none" stroke="var(--orange)" stroke-width="1.2"/><circle cx="6" cy="9.6" r=".7" fill="var(--orange)"/></svg>
        555.210.4417
      </li>
      <li>
        <svg viewBox="0 0 12 12" aria-hidden="true"><path d="M1 4c0-2 2-3 5-3s5 1 5 3l-2 1-1-1.5H4L3 5z" fill="var(--orange)"/><rect x="2.5" y="6" width="7" height="5" rx="1" fill="var(--orange)"/></svg>
        555.308.2290
      </li>
      <li>
        <svg viewBox="0 0 12 12" aria-hidden="true"><rect x=".5" y="2" width="11" height="8" fill="var(--orange)"/><path d="M.5 2.5 6 7l5.5-4.5" fill="none" stroke="#fff" stroke-width="1"/></svg>
        info@harlowfreight.com
      </li>
      <li>
        <svg viewBox="0 0 12 12" aria-hidden="true"><circle cx="6" cy="6" r="5.5" fill="var(--orange)"/><ellipse cx="6" cy="6" rx="2.3" ry="5.5" fill="none" stroke="#fff" stroke-width=".8"/><path d="M.5 6h11" stroke="#fff" stroke-width=".8"/></svg>
        www.harlowfreight.com
      </li>
    </ul>
  </div>

  <div class="address-band">
    <svg class="pin" viewBox="0 0 12 16" aria-hidden="true"><path d="M6 0a6 6 0 0 0-6 6c0 4.5 6 10 6 10s6-5.5 6-10a6 6 0 0 0-6-6z" fill="var(--orange)"/><circle cx="6" cy="6" r="2.2" fill="var(--navy)"/></svg>
    Marlow Court, 14 Keel Street, London, E2 4RT
    <svg class="band-chevrons" viewBox="0 0 70 40" aria-hidden="true">
      <path d="M2 4h14l10 14-10 14H2l10-14z" fill="var(--orange)"/>
      <path d="M24 4h14l10 14-10 14H24l10-14z" fill="#fff"/>
      <path d="M46 4h14l10 14-10 14H46l10-14z" fill="var(--orange)"/>
    </svg>
  </div>
</section>

<section class="card card-back" aria-label="Business card back">
  <div class="back-brand"><span class="brand-dot"></span>HARLOW FREIGHT</div>
</section>

</body>
</html>
```